Fence Contractor Website Design

We are working with Yard Shield. They are a local fencing and automatic gate installer and in need of a new website design.
Some sites to use for inspiration:
https://pelmorfence.example
https://tarvikfence.example
https://www.bristowdecksandfence.example
https://www.railquestinc.example
Thank you for taking the time to consider designing a website for us. We are web developers based in Stockton, CA, USA. Most of our projects go through the same process. Understanding this process may help you win a project with us. We custom-code all of our websites in-house. We don’t have any requirements as to what tools you use for your design, but we prefer Figma files. For any design that we label as four-stars, we send it to the client for review. The client picks the final design they want us to use. Once we complete this process, we will continue to show additional clients all the four-star sites and purchase them later. Your designs will have multiple chances to sell. For better chances of success, we ask that you follow these guidelines.
IMAGES:
If you use any images or icons in the design, we ask that you have a link to the asset so we can purchase the image/icon. Most of the designs we submit do not have the customer’s images on them unless they have some great images. Be creative; show us the feeling you are trying to portray with your image choices. Use any royalty-free site you choose. We subscribe to Veltrix and mainly use their images, but we can purchase images outside of Veltrix.
PLEASE NOTE: we will not submit designs to clients with watermarks on the images.
FONTS:
We ask that you identify the fonts used in the design. This can be done in a message if you want. We typically use Google Fonts and Veltrix Fonts.
CONTENT:
We're always open to different content and ideas. We often submit designs with stock images so the client can see our vision. We typically take pictures after the website launch to use their images with our vision. Lorem Ipsum is fine for paragraphs, but we ask that you write the headers in correct English. We want to be able to show the vision and identify the sections of the website.
INSPIRATION:
We typically add a couple of links in the brief of websites we like to help you get started in your design.
REVISIONS:
We do not often ask for revisions of the designs unless we see something in the design that may not appeal to the client. If there are slight changes that we want to make, we do that in the development process.
FEEDBACK:
We rarely give feedback on designs during the design process. We are working on many website projects and do not have the time to provide feedback. We usually respond if your request is well thought out and asks specific questions, but a note asking “feedback, please” usually goes unanswered.

```html
<!DOCTYPE html>
<html lang="en">
<head>
<meta charset="utf-8">
<title>Yard Shield — Fencing &amp; Gates</title>
<link href="https://fonts.googleapis.com/css2?family=Russo+One&family=Roboto:wght@400;500;700&family=Poppins:wght@500;600&display=swap" rel="stylesheet">
<style>
:root{
  --navy:#1b2240;
  --navy-deep:#141a33;
  --red:#e8141b;
  --ink:#2b2b2b;
  --muted:#5c5f68;
  --grey:#8a8d94;
  --card:#f1f1f1;
  --gold:#f3a71b;
  --white:#fff;
}
*{margin:0;padding:0;box-sizing:border-box}
html,body{width:1200px;height:4402px;overflow:hidden}
body{font-family:'Roboto',sans-serif;color:var(--ink);background:var(--white);position:relative}
.abs{position:absolute}
.display{font-family:'Russo One',sans-serif;letter-spacing:6px;text-transform:uppercase}
.btn{position:absolute;display:flex;align-items:center;padding-left:18px;font:700 14px 'Poppins',sans-serif;text-transform:uppercase;color:var(--white);background:var(--red);clip-path:polygon(0 0,90% 0,100% 50%,90% 100%,0 100%)}
.btn.navy{background:var(--navy)}
.center{left:0;width:1200px;text-align:center}

/* header */
.site-header{position:absolute;top:0;left:0;width:1200px;height:125px;background:var(--white)}
.brand{position:absolute;left:111px;top:44px;display:flex;align-items:center;gap:10px;font:26px 'Russo One',sans-serif;color:var(--navy)}
.brand i{width:22px;height:22px;background:var(--red);display:block}
.phone{position:absolute;left:458px;top:26px;display:flex;align-items:center;gap:12px;font:500 25px 'Poppins',sans-serif;color:var(--navy)}
.nav{position:absolute;left:437px;top:87px;display:flex;gap:29px;font:500 14px 'Roboto',sans-serif;color:var(--navy);text-transform:uppercase}
.nav .active{color:var(--red);border-bottom:2px solid var(--red);padding-bottom:2px}

/* hero */
.hero{position:absolute;top:125px;left:0;width:1200px;height:598px;
  background:
    radial-gradient(ellipse 520px 260px at 1080px 560px,rgba(120,160,70,.95),rgba(120,160,70,0) 70%),
    radial-gradient(ellipse 700px 300px at 1000px 120px,rgba(40,70,35,.9),rgba(40,70,35,0) 70%),
    linear-gradient(170deg,#2a2f2c 0%,#181b1a 40%,#1f2a1c 65%,#4d6d2f 100%)}
.hero::after{content:"";position:absolute;inset:0;background:rgba(0,0,0,.18)}
.hero > *{z-index:1}
.hero h1{position:absolute;top:152px;font-size:45px;line-height:52px;color:var(--white);font-weight:400}
.hero p{position:absolute;top:322px;font-size:17px;line-height:26px;color:var(--white)}

/* section titles */
.sec-title{position:absolute;font:34px 'Russo One',sans-serif;letter-spacing:4px;text-transform:uppercase;color:var(--navy)}
.sec-title em{font-style:normal;color:var(--red)}
.kicker{position:absolute;font:500 19px 'Roboto',sans-serif;text-transform:uppercase;color:var(--grey);display:flex;align-items:center;gap:10px;justify-content:center}
.kicker b{display:block;width:52px;height:2px;background:currentColor}

/* about */
.about{position:absolute;top:723px;left:0;width:1200px;height:649px}
.about .frame{position:absolute;left:108px;top:120px;width:406px;height:406px;background:var(--navy);padding:14px}
.about .frame .shot{width:100%;height:100%;background:
    radial-gradient(ellipse 260px 120px at 70% 22%,rgba(235,238,240,.9),rgba(235,238,240,0) 70%),
    linear-gradient(180deg,#c9d0d4 0%,#aab3b7 30%,#3e4a3b 45%,#2b2f33 62%,#556b3a 78%,#6f8a45 100%)}
.about .frame::after{content:"";position:absolute;left:0;right:0;bottom:-10px;height:10px;background:var(--red)}
.about p{position:absolute;left:598px;width:500px;font-size:15.5px;line-height:28px;color:var(--muted)}

/* why */
.why{position:absolute;top:1372px;left:0;width:1200px;height:602px;background:
    radial-gradient(ellipse 500px 250px at 260px 140px,rgba(70,80,110,.45),rgba(70,80,110,0) 70%),
    linear-gradient(180deg,#232a45,#222944 60%,#1b2138)}
.feature{position:absolute;top:294px;width:240px;text-align:center;color:var(--white)}
.feature .ring{width:103px;height:103px;margin:0 auto;border-radius:50%;background:#8b8d93;border:4px solid #c9cacd;display:flex;align-items:center;justify-content:center}
.feature h3{margin-top:26px;font:15px 'Russo One',sans-serif;letter-spacing:2px;line-height:24px;text-transform:uppercase}
.feature p{margin-top:8px;font-size:14px;line-height:24px}

/* services */
.services{position:absolute;top:1974px;left:0;width:1200px;height:906px}
.svc{position:absolute;top:243px;width:308px;height:568px;filter:drop-shadow(0 4px 10px rgba(0,0,0,.18))}
.svc .body{position:absolute;inset:0;background:var(--white);clip-path:polygon(50% 0,100% 7%,100% 89.5%,50% 100%,0 89.5%,0 7%)}
.svc .photo{position:absolute;left:0;top:0;width:308px;height:310px;clip-path:polygon(50% 0,100% 8%,100% 86%,50% 100%,0 86%,0 8%)}
.svc h3{position:absolute;top:343px;width:100%;text-align:center;font:14px 'Russo One',sans-serif;letter-spacing:1.5px;line-height:22px;color:var(--navy);text-transform:uppercase}
.svc p{position:absolute;top:393px;left:20px;right:20px;text-align:center;font-size:14.5px;line-height:22px;color:var(--ink)}
.svc .btn{top:468px;left:94px;width:120px;height:36px;font-size:12px;padding-left:16px}
.svc svg.edge{position:absolute;left:0;top:505px}
.arrow-c{position:absolute;width:26px;height:26px;border:1.5px solid #333;border-radius:50%;display:flex;align-items:center;justify-content:center}

/* cta */
.cta{position:absolute;top:2880px;left:0;width:1200px;height:560px;background:
    radial-gradient(ellipse 500px 260px at 250px 120px,rgba(70,80,110,.4),rgba(70,80,110,0) 70%),
    linear-gradient(180deg,#222944,#1b2138);overflow:hidden}
.cta .shot{position:absolute;inset:0;background:
    radial-gradient(ellipse 260px 90px at 1100px 60px,rgba(120,150,80,.8),rgba(120,150,80,0) 70%),
    linear-gradient(180deg,#4f7fbf 0%,#93b2d6 20%,#3a3e44 30%,#2a2f35 58%,#7f8286 72%,#a7a9ab 100%);
  clip-path:polygon(675px 0,1200px 0,1200px 560px,697px 560px,597px 280px)}
.cta .stripe{position:absolute;inset:0;background:var(--red);clip-path:polygon(660px 0,675px 0,597px 280px,697px 560px,680px 560px,582px 280px)}
.cta h2{position:absolute;left:111px;top:105px;font:36px 'Russo One',sans-serif;letter-spacing:3px;color:var(--white)}
.cta .kicker{left:111px;top:150px;justify-content:flex-start;font-size:24px;text-transform:none;color:#8d919c;font-weight:700}
.cta p{position:absolute;left:111px;width:420px;font-size:14.5px;line-height:23px;color:var(--white)}

/* testimonials */
.reviews{position:absolute;top:3440px;left:0;width:1200px;height:537px}
.review{position:absolute;top:214px;width:303px;height:220px;background:var(--card)}
.avatar{position:absolute;left:22px;top:26px;width:68px;height:68px;border-radius:50%;display:flex;align-items:center;justify-content:center;color:var(--white);font:500 22px 'Roboto',sans-serif}
.review h4{position:absolute;left:108px;top:30px;font:500 15px 'Roboto',sans-serif;text-transform:uppercase;color:var(--ink)}
.review .when{position:absolute;left:108px;top:56px;font-size:12px;color:var(--grey);text-transform:uppercase}
.review .stars{position:absolute;left:108px;top:72px;font-size:17px;color:var(--gold);letter-spacing:1px}
.review p{position:absolute;left:20px;top:128px;right:20px;font-size:14px;line-height:21px;color:#8a8a8a}

/* footer */
.site-footer{position:absolute;top:3977px;left:0;width:1200px;height:425px;background:var(--navy);color:var(--white)}
.site-footer h4{position:absolute;top:62px;font:500 21px 'Roboto',sans-serif}
.links{position:absolute;top:98px;list-style:none;font-size:14.5px}
.links li{height:31px;display:flex;align-items:center;gap:14px}
.links li::before{content:"";width:10px;height:10px;background:var(--white);clip-path:polygon(0 35%,50% 35%,50% 0,100% 50%,50% 100%,50% 65%,0 65%)}
.contact-row{position:absolute;left:508px;display:flex;align-items:center;gap:12px;font-size:14.5px}
.contact-row .dot{width:34px;height:34px;border-radius:50%;background:var(--red);display:flex;align-items:center;justify-content:center}
.rule{position:absolute;left:97px;top:364px;width:1004px;height:1px;background:#6a7089}
</style>
</head>
<body>

<header class="site-header">
  <div class="brand"><i></i>YARD SHIELD</div>
  <div class="phone">
    <svg width="36" height="36" viewBox="0 0 36 36"><circle cx="18" cy="18" r="17" fill="var(--navy)"/><path d="M12 10c2 0 3 4 2 5l-1 1c1 2 3 4 5 5l1-1c1-1 5 0 5 2 0 2-2 4-4 3-5-1-10-6-11-11-1-2 1-4 3-4z" fill="#fff"/></svg>
    (123) 456-7890
  </div>
  <div class="btn navy" style="left:718px;top:20px;width:171px;height:45px;font-size:15px;font-weight:500;padding-left:19px">Free Estimate</div>
  <div class="btn" style="left:909px;top:20px;width:180px;height:45px;font-size:14px;font-weight:600;padding-left:16px">Get a Free Quote</div>
  <nav class="nav">
    <span class="active">Home</span><span>About Us</span><span>Fence &amp; Gate</span><span>Automatic Gate Installer</span><span>Contact Us</span>
  </nav>
</header>

<section class="hero" role="img" aria-label="Black metal fence along a green lawn">
  <h1 class="center display">Strong. Secure. Stylish.<br>Yard Shield has you<br>covered.</h1>
  <p class="center">Trusted local experts in fencing &amp; automatic gate installation. Serving homeowners<br>and businesses with quality craftsmanship and unbeatable service.</p>
  <div class="btn" style="left:492px;top:393px;width:214px;height:41px;font-size:14px">Request a Free Quote</div>
  <svg class="abs" style="left:589px;top:490px" width="22" height="54" viewBox="0 0 22 54"><rect x="2" y="2" width="18" height="28" rx="9" fill="none" stroke="#fff" stroke-width="2"/><line x1="11" y1="8" x2="11" y2="14" stroke="#fff" stroke-width="2"/><path d="M11 36v14M6 45l5 5 5-5" fill="none" stroke="#fff" stroke-width="2"/></svg>
</section>

<section class="about">
  <div class="frame"><div class="shot" role="img" aria-label="Dark slatted driveway gate set between green hedges"></div></div>
  <h2 class="sec-title" style="left:598px;top:142px">About <em>Us</em></h2>
  <div class="kicker" style="left:598px;top:193px;color:var(--muted)">Who We Are <b></b></div>
  <p style="top:230px">Yard Shield is a locally owned fencing and gate company dedicated to protecting what matters most — your home, your family, and your business.</p>
  <p style="top:343px">With over X years of experience, we combine top-quality craftsmanship with customer-first service.To provide strong, secure, and stylish fencing solutions that stand the test of time.</p>
  <div class="btn" style="left:598px;top:451px;width:139px;height:43px;font-size:13px">Learn More</div>
</section>

<section class="why" role="img" aria-label="Dark navy tinted photo of a wooden fence">
  <h2 class="sec-title center" style="top:118px;color:var(--white);font-size:29px">Why Choose Yard Shield?</h2>
  <div class="kicker center" style="top:162px;color:#8a8f9e"><b></b>What We Serve<b></b></div>
  <p class="abs center" style="top:203px;font-size:16px;line-height:25px;color:var(--white)">Yard Shield is a locally owned fencing and gate company dedicated to protecting what matters<br>most — your home, your family, and your business.</p>
  <div class="feature" style="left:89px">
    <div class="ring"><svg width="46" height="46" viewBox="0 0 46 46"><path d="M9 24l9 9 20-20" fill="none" stroke="#fff" stroke-width="4"/></svg></div>
    <h3>Local and<br>Trusted</h3><p>Proudly serving [City/Region]<br>for over X years.</p>
  </div>
  <div class="feature" style="left:350px">
    <div class="ring"><svg width="46" height="46" viewBox="0 0 46 46"><rect x="8" y="10" width="30" height="26" fill="none" stroke="#fff" stroke-width="3"/><path d="M14 10v26M20 10v26M26 10v26M32 10v26" stroke="#fff" stroke-width="2"/></svg></div>
    <h3>Quality<br>Materials</h3><p>Built to last with top-grade<br>wood, steel, and vinyl.</p>
  </div>
  <div class="feature" style="left:611px">
    <div class="ring"><svg width="46" height="46" viewBox="0 0 46 46"><circle cx="23" cy="23" r="9" fill="none" stroke="#fff" stroke-width="4"/><path d="M23 6v6M23 34v6M6 23h6M34 23h6M11 11l4 4M31 31l4 4M35 11l-4 4M15 31l-4 4" stroke="#fff" stroke-width="3"/></svg></div>
    <h3>Expert<br>Installation</h3><p>Licensed, insured, and highly<br>trained crews.</p>
  </div>
  <div class="feature" style="left:871px">
    <div class="ring"><svg width="46" height="46" viewBox="0 0 46 46"><circle cx="23" cy="15" r="6" fill="#fff"/><circle cx="11" cy="19" r="4" fill="#fff"/><circle cx="35" cy="19" r="4" fill="#fff"/><path d="M13 36c0-8 4-12 10-12s10 4 10 12zM4 34c0-6 3-8 7-8M42 34c0-6-3-8-7-8" fill="#fff" stroke="#fff" stroke-width="2"/></svg></div>
    <h3>Customer<br>Satisfaction</h3><p>Proudly serving [City/Region]<br>for over X years.</p>
  </div>
</section>

<section class="services">
  <h2 class="sec-title center" style="top:100px">Our <em>Services</em></h2>
  <div class="kicker center" style="top:140px;color:var(--muted);font-size:18px"><b></b>What We Offer<b></b></div>
  <p class="abs center" style="top:180px;font-size:15px;line-height:24px">Yard Shield is a locally owned fencing and gate company dedicated to protecting what matters<br>most — your home, your family, and your business.</p>

  <div class="arrow-c" style="left:42px;top:484px"><svg width="10" height="10" viewBox="0 0 10 10"><path d="M7 1L3 5l4 4" fill="none" stroke="#333" stroke-width="1.6"/></svg></div>
  <div class="arrow-c" style="left:1130px;top:484px"><svg width="10" height="10" viewBox="0 0 10 10"><path d="M3 1l4 4-4 4" fill="none" stroke="#333" stroke-width="1.6"/></svg></div>

  <div class="svc" style="left:111px">
    <div class="body"></div>
    <div class="photo" role="img" aria-label="Modern metal and wood privacy fence panels" style="background:linear-gradient(180deg,#c9ccce 0%,rgba(201,204,206,0) 30%),linear-gradient(90deg,#7e8487 0%,#a3a7a8 22%,#9c7c58 42%,#7a5b3e 60%,#8d9194 78%,#b3b7b9 100%)"></div>
    <h3>Commercial &amp; Industrial<br>Fencing</h3>
    <p>Chain link, steel, and high-security options designed to keep businesses safe and secure.</p>
    <div class="btn navy">Learn More</div>
    <svg class="edge" width="308" height="63"><polyline points="0,4 154,60 308,4" fill="none" stroke="var(--navy)" stroke-width="4"/></svg>
  </div>
  <div class="svc" style="left:446px">
    <div class="body"></div>
    <div class="photo" role="img" aria-label="Grey horizontal slat gate in front of a modern house" style="background:linear-gradient(180deg,#2f3338 0%,#3d4247 30%,#5d6267 55%,#8c9094 80%,#a9acae 100%)"></div>
    <h3>Automatic Gates &amp; Access<br>Control</h3>
    <p>Chain link, steel, and high-security options designed to keep businesses safe and secure.</p>
    <div class="btn">Learn More</div>
    <svg class="edge" width="308" height="63"><polyline points="0,4 154,60 308,4" fill="none" stroke="var(--red)" stroke-width="4"/></svg>
  </div>
  <div class="svc" style="left:781px">
    <div class="body"></div>
    <div class="photo" role="img" aria-label="Worker drilling into a new wooden picket fence" style="background:radial-gradient(ellipse 90px 70px at 90px 200px,rgba(180,40,40,.55),rgba(180,40,40,0) 70%),linear-gradient(90deg,#efe3c6,#e0cfa8 55%,#b5b98c 80%,#7e935a)"></div>
    <h3>Repairs &amp;<br>Maintenance</h3>
    <p>Chain link, steel, and high-security options designed to keep businesses safe and secure.</p>
    <div class="btn navy">Learn More</div>
    <svg class="edge" width="308" height="63"><polyline points="0,4 154,60 308,4" fill="none" stroke="var(--navy)" stroke-width="4"/></svg>
  </div>
</section>

<section class="cta">
  <div class="shot" role="img" aria-label="Dark slatted sliding gate at a house with a paved driveway"></div>
  <div class="stripe"></div>
  <h2>Call us today</h2>
  <div class="kicker">Free Estimate <b style="width:58px"></b></div>
  <p style="top:207px">Lorem ipsum dolor sit amet, consectetur adipiscing elit, sed do eiusmod tempor incididunt ut labore et dolore magna aliqua. Ut enim ad minim veniam, quis nostrud exercitation ullamco laboris nisi ut aliquip ex ea commodo consequat.</p>
  <p style="top:321px">Duis aute irure dolor in reprehenderit in voluptate velit esse cillum dolore eu fugiat nulla pariaturcupidatat non proident, mollit anim id est laborum.</p>
  <div class="btn" style="left:111px;top:407px;width:287px;height:42px;font-size:14px">Request a Free Estimate Now</div>
</section>

<section class="reviews">
  <h2 class="sec-title center" style="top:122px">Client <em>Testimonials</em></h2>
  <div class="kicker center" style="top:161px;color:var(--muted);font-size:18px"><b></b>Client Reviews<b></b></div>
  <div class="arrow-c" style="left:49px;top:316px;border-color:#aaa"><svg width="10" height="10" viewBox="0 0 10 10"><path d="M7 1L3 5l4 4" fill="none" stroke="#aaa" stroke-width="1.6"/></svg></div>
  <div class="arrow-c" style="left:1125px;top:316px"><svg width="10" height="10" viewBox="0 0 10 10"><path d="M3 1l4 4-4 4" fill="none" stroke="#333" stroke-width="1.6"/></svg></div>

  <article class="review" style="left:111px">
    <div class="avatar" style="background:#1a73c7">MQ</div>
    <h4>Marla Quenby</h4><div class="when">A year ago</div><div class="stars">★★★★★</div>
    <p>Lorem ipsum dolor sit amet, consectetur adipiscing elit, sed do eiusmod tempor incididunt ut labore et dolore magna aliqua.</p>
  </article>
  <article class="review" style="left:448px">
    <div class="avatar" style="background:#c4331d">DV</div>
    <h4>Delia Voss</h4><div class="when">A year ago</div><div class="stars">★★★★★</div>
    <p>Lorem ipsum dolor sit amet, consectetur adipiscing elit, sed do eiusmod tempor incididunt ut labore et dolore magna aliqua.</p>
  </article>
  <article class="review" style="left:786px">
    <div class="avatar" style="background:#3e9c3a">NT</div>
    <h4>Nora Tillman</h4><div class="when">A year ago</div><div class="stars">★★★★★</div>
    <p>Lorem ipsum dolor sit amet, consectetur adipiscing elit, sed do eiusmod tempor incididunt ut labore et dolore magna aliqua.</p>
  </article>
</section>

<footer class="site-footer">
  <h4 style="left:97px">Quick Links</h4>
  <ul class="links" style="left:99px"><li>Home</li><li>About Us</li><li>Fence &amp; Gate</li><li>Gate Installer</li><li>Contact Us</li></ul>
  <h4 style="left:296px">Other Links</h4>
  <ul class="links" style="left:298px"><li>FAQ</li><li>Terms of Use</li><li>Privacy Policy</li><li>Support Links</li><li>Conditions</li></ul>
  <h4 style="left:508px">Contact Us</h4>
  <div class="contact-row" style="top:109px"><span class="dot"><svg width="14" height="16" viewBox="0 0 14 16"><path d="M7 0a6 6 0 0 0-6 6c0 4 6 10 6 10s6-6 6-10a6 6 0 0 0-6-6z" fill="#fff"/><circle cx="7" cy="6" r="2" fill="var(--red)"/></svg></span>Company Name,United State.</div>
  <div class="contact-row" style="top:169px"><span class="dot"><svg width="16" height="12" viewBox="0 0 16 12"><rect width="16" height="12" rx="1" fill="#fff"/><path d="M1 1l7 6 7-6" fill="none" stroke="var(--red)" stroke-width="1.5"/></svg></span>info@companyname.in</div>
  <div class="contact-row" style="top:229px"><span class="dot"><svg width="14" height="14" viewBox="0 0 14 14"><path d="M3 1c1 0 2 3 1 4l-1 1c1 2 2 3 4 4l1-1c1-1 4 0 4 1 0 2-1 3-3 3C5 13 1 9 1 4c0-2 1-3 2-3z" fill="#fff"/></svg></span>+1888 8888 8888</div>
  <h4 style="left:827px">Sign Up To Our Newsletter</h4>
  <p class="abs" style="left:829px;top:106px;width:280px;font-size:14.5px;line-height:30px">Lorem ipsum dolor sit amet,consectetur adipiscing elit,adipiscing elit.</p>
  <div class="abs" style="left:830px;top:179px;width:271px;padding-bottom:8px;border-bottom:1.5px solid #fff;font-size:14.5px">Email</div>
  <div class="btn" style="left:834px;top:241px;width:137px;height:50px;font:500 17px 'Roboto',sans-serif;text-transform:none;padding-left:20px">Subscribe</div>
  <div class="rule"></div>
  <p class="abs center" style="top:385px;font-size:14px">Copyrights@2025.Yard Shield.All Rights Reserved</p>
</footer>

</body>
</html>
```